Building Referrer Relationships Booklet

4 page A4 booklet to give to potential professional referrers to establish a collaborative relationship.Needs to be bright, vibrant, colourful, friendly, inviting, in keeping with The Linden Practice colours.
Want to provide potential referrer partners a great reason to choose to collaborate with us. They need to know who we are, what makes us different/appealing, and who we are looking for to connect with.
The final product should communicate high performance and connectedness.
Updates

Target Market(s)

professional medical allied health and fitness practitioners

Industry/Entity Type

Health

Requirements
Must have
• energetic, vibrant, engaging, inviting, images

```html
<!DOCTYPE html>
<html lang="en">
<head>
<meta charset="utf-8">
<title>Referral Partnerships Booklet – The Linden Practice</title>
<link rel="stylesheet" href="https://fonts.googleapis.com/css2?family=Poppins:wght@400;500&family=Source+Sans+3:wght@400;600;700&display=swap">
<style>
:root{
  --backdrop:#e4e4e4;
  --paper:#f8f8f7;
  --navy:#1f3d4f;
  --green:#9fd49a;
  --teal:#4f8a78;
  --ink:#1b1b1b;
  --accent:#d0212b;
  --photo-a:#6f8fb0;
  --photo-b:#c9a27e;
  --collage-a:#8a7a6c;
  --collage-b:#c86a4c;
}
*{box-sizing:border-box;margin:0;padding:0}
html,body{width:1200px;height:675px;overflow:hidden;background:var(--backdrop)}
body{font-family:"Source Sans 3",Arial,sans-serif;color:var(--ink);position:relative}
.page{position:absolute;top:132px;width:290px;height:410px;background:var(--paper);overflow:hidden;box-shadow:0 1px 3px rgba(0,0,0,.18)}
.page--cover{left:15px}.page--about{left:305px}.page--method{left:605px}.page--partners{left:895px}
.page__frame{position:absolute;inset:0;width:100%;height:100%}
.block{position:absolute}
.small{font-size:4.7px;line-height:6.2px}
.tiny{font-size:2.8px;line-height:4px}
b{font-weight:700}

/* cover */
.cover__title{left:58px;top:76px;font-family:"Poppins",sans-serif;font-weight:500;font-size:11px;line-height:12px}
.cover__lead{left:58px;top:121px;font-family:"Poppins",sans-serif;font-size:5.2px}
.cover__photo{left:41px;top:153px;width:203px;height:134px;background:linear-gradient(135deg,var(--photo-a),var(--photo-b) 60%,#a17a55)}
.cover__closing{left:0;width:290px;top:306px;text-align:center;font-family:"Poppins",sans-serif;font-size:7.2px}

/* about */
.about__values{left:32px;top:59px;width:245px}
.about__values p{margin-bottom:6.2px}
.about__passion{left:20px;width:250px;top:183px;text-align:center;font-size:6.6px;line-height:9px}
.about__top{left:0;width:290px;top:212px;text-align:center}
.about__list{left:84px;top:230px;list-style:none}
.about__list li{display:flex;gap:8px}
.about__list .tiny{padding-left:18px;margin-bottom:3px}
.about__team{left:28px;top:299px}
.about__team h3{font-weight:400;font-size:6.2px;margin-bottom:1px}
.about__team p{font-size:4.6px;line-height:7.6px;font-weight:700}

/* method */
.method__title{left:0;width:290px;top:34px;text-align:center;font-family:"Poppins",sans-serif;font-weight:500;font-size:7.6px;color:var(--accent)}
.method__intro{left:25px;top:58px;width:245px}
.method__steps{left:7px;top:84px;width:180px}
.label{color:var(--accent);margin:0 0 8px}
.step{padding-left:15px;margin-bottom:3px}
.step__items{padding-left:46px;margin-bottom:7px}
.step__items--deep{padding-left:51px}
.method__collage{left:183px;top:215px;width:83px;height:125px;border:1px solid #fff;background:linear-gradient(160deg,var(--collage-a),var(--collage-b) 45%,#b58e6a 70%,#5d5048)}

/* partners */
.stat{top:57px;width:108px;height:84px;background:var(--navy);color:#fff;padding:8px 7px;font-size:3.3px;line-height:6px}
.stat--team{left:36px}.stat--elite{left:149px;width:108px}
.stat ul{list-style:none;margin-top:5px;line-height:6px}
.stat--team li::before{content:"•";margin-right:2px}
.stat--elite p{margin-bottom:3px}
.partners__heading{left:0;width:296px;top:152px;text-align:center;font-size:5.8px}
.partners__list{left:31px;top:166px;width:250px;list-style:none;font-size:4.5px;line-height:7.7px}
.partners__list li::before{content:"•";margin-right:3px;font-size:3.5px}
.partners__list .sub{padding-left:19px;display:block}
.partners__list .sub::before{content:none}
.badges{left:52px;top:343px;display:flex;gap:12px;align-items:center}
.badge{background:var(--navy)}
.badge--ring{width:12px;height:14px;border-radius:50%;background:#c8323a}
.badge--wide{width:46px;height:12px;background:#2a4f9c}
.badge--tri{width:18px;height:15px;background:var(--accent);clip-path:polygon(50% 0,100% 100%,0 100%)}
.badge--wide-red{width:48px;height:12px;background:var(--accent)}
.badge--square{width:15px;height:18px;background:#223a57}
</style>
</head>
<body>

<section class="page page--cover">
  <svg class="page__frame" viewBox="0 0 290 410" preserveAspectRatio="none" aria-hidden="true">
    <polygon points="0,0 200,0 0,54" fill="var(--navy)"/>
    <polygon points="110,0 290,0 290,52" fill="var(--green)"/>
    <polygon points="110,0 200,0 153.5,12.6" fill="var(--teal)"/>
    <polygon points="0,355 0,410 175,410" fill="var(--green)"/>
    <polygon points="290,352 290,410 120,410" fill="var(--navy)"/>
    <polygon points="120,410 175,410 146.4,401" fill="var(--teal)"/>
  </svg>
  <h1 class="block cover__title">Referral Partnerships<br>Because Together We Achieve More</h1>
  <p class="block cover__lead">We are here to help our clients get back on their feet.</p>
  <div class="block cover__photo" role="img" aria-label="Team of hands stacked together in the centre"></div>
  <p class="block cover__closing">Let’s combine our skillsets so we can achieve even better results.</p>
</section>

<section class="page page--about">
  <svg class="page__frame" viewBox="0 0 290 410" preserveAspectRatio="none" aria-hidden="true">
    <polygon points="0,0 200,0 0,54" fill="var(--navy)"/>
    <polygon points="110,0 290,0 290,52" fill="var(--green)"/>
    <polygon points="110,0 200,0 153.5,12.6" fill="var(--teal)"/>
    <polygon points="0,355 0,410 175,410" fill="var(--green)"/>
    <polygon points="290,352 290,410 120,410" fill="var(--navy)"/>
    <polygon points="120,410 175,410 146.4,401" fill="var(--teal)"/>
  </svg>
  <div class="block about__values small">
    <p>About Us:</p>
    <p>COURAGE INSPIRATION &nbsp;FUN &nbsp; CREATIVE &nbsp;WOW TEAM</p>
    <p><b>Courage</b> gives us the strength and confidence to take risks and embrace challenges</p>
    <p><b>Inspiration</b> is our energy, our fuel for success, that life force that feeds us as we grow and develop.</p>
    <p><b>Fun</b> generates happiness, and we all function at our best when we are happy.</p>
    <p><b>Creativity</b> sets us as an innovative leading-edge business.</p>
    <p><b>Wow</b> means being the very best we can be and realise our true potential. We are not your average business, our service is not average, and our people are not average.</p>
    <p><b>Team</b> and in particular high-performance team means we perform at our very best. Great teamwork creates unity and we accomplish much more than each of us alone.</p>
  </div>
  <p class="block about__passion">At The Linden Practice, we are passionate about building strong postural foundations, from the feet up</p>
  <p class="block about__top small">The top 3 things our clients love about us (and hopefully yours will too!):</p>
  <ol class="block about__list small">
    <li><span>1.</span><span>Positive energy, enthusiasm and outcomes</span></li>
    <li class="tiny">NPS average score &gt;9 out of 10</li>
    <li><span>2.</span><span>Trusted leader in the practice of podiatric medicine</span></li>
    <li class="tiny">established 1999, elite experience, latest high-tech equipment</li>
    <li><span>3.</span><span>Focus is on strong feet, not just orthotics!</span></li>
    <li class="tiny">Barefoot Technology, Fascial Lines, Foot Manual Therapies</li>
  </ol>
  <div class="block about__team">
    <h3>Our Team:</h3>
    <p>Dr Marcus Vellaran (Principal Podiatrist)<br>
    Dr Hannah Corby (Senior Podiatrist)<br>
    Dr Olivia Prentice (Podiatrist)<br>
    Dr Tobias Leung (Podiatrist)<br>
    Jodie Harlow (Practice Manager)<br>
    Renee Calder (Front Office Administrator)</p>
  </div>
</section>

<section class="page page--method">
  <svg class="page__frame" viewBox="0 0 290 410" preserveAspectRatio="none" aria-hidden="true">
    <polygon points="0,0 200,0 0,54" fill="var(--navy)"/>
    <polygon points="110,0 290,0 290,52" fill="var(--green)"/>
    <polygon points="110,0 200,0 153.5,12.6" fill="var(--teal)"/>
    <polygon points="0,355 0,410 175,410" fill="var(--green)"/>
    <polygon points="290,352 290,410 120,410" fill="var(--navy)"/>
    <polygon points="120,410 175,410 146.4,401" fill="var(--teal)"/>
  </svg>
  <h2 class="block method__title">The Linden Practice Way</h2>
  <p class="block method__intro small">Our pathway to strengthen postural foundations, to create lasting changes for freedom of movement, and ultimately keep us going well beyond what we thought was possible (updated as research and tech changes).</p>
  <div class="block method__steps small">
    <p class="label">Fix Your Feet</p>
    <p class="step">1. <b>Fix</b> the pain</p>
    <p class="step__items">Provide analgesia<br>Reduce inflammation<br>Corn/callus/foreign body removal<br>Ingrown/thickened toenail repair and maintenance<br>Surgery</p>
    <p class="step">2. <b>Protect</b> the feet (reduce damage, optimise stability, promote healing)</p>
    <p class="step__items">Reduce tissue damage<br>Optimise Foot Posture<br>Activate neuromuscular/reflexive balance stability<br>Promote tissue repair/cellular regeneration</p>
    <p class="step">3. <b>Strengthen</b> the feet (increase strength and resilience)</p>
    <p class="step__items">Strengthen intrinsics<br>Connect foot strength to core strength<br>Stimulate neuromuscular strength</p>
    <p class="label">Biohack Your Body</p>
    <p class="step" style="padding-left:20px">4. <b>Protect</b> the whole body (stability)</p>
    <p class="step__items step__items--deep">Optimise Postural Alignment<br>Activate neuromuscular/reflexive balance stability<br>Customised corrective exercises<br>Improve cellular regeneration<br>Optimise nutrition/healthy gut<br>Optimise healthy mind</p>
    <p class="step" style="padding-left:20px">5. <b>Strengthen</b> the whole body (strength, elasticity)</p>
    <p class="step__items step__items--deep" style="padding-left:55px">Strengthen the deep core (stabilisers)<br>Strengthen the outer core (mobilisers)<br>Increase fascial elasticity/strength<br>Increase functional strength<br>Increase endurance<br>Customised nutrition for specific performance<br>Improve psychological resilience</p>
    <p class="step" style="padding-left:21px">6. <b>Repeat</b> consistently</p>
  </div>
  <div class="block method__collage" role="img" aria-label="Collage of team photos and workshop sessions"></div>
</section>

<section class="page page--partners">
  <svg class="page__frame" viewBox="0 0 290 410" preserveAspectRatio="none" aria-hidden="true">
    <polygon points="0,0 200,0 0,54" fill="var(--navy)"/>
    <polygon points="110,0 290,0 290,52" fill="var(--green)"/>
    <polygon points="110,0 200,0 153.5,12.6" fill="var(--teal)"/>
    <polygon points="0,355 0,410 175,410" fill="var(--green)"/>
    <polygon points="290,352 290,410 120,410" fill="var(--navy)"/>
    <polygon points="120,410 175,410 146.4,401" fill="var(--teal)"/>
  </svg>
  <div class="block stat stat--team">
    <p>Our Team Achievements:</p>
    <ul>
      <li>Director, Sports Medicine Network (SMN)</li>
      <li>Director, Regional Academy of Foot &amp; Sports Medicine (RAFSM)</li>
      <li>External Advisor, Westbrook University Podiatric Unit</li>
      <li>BMA Level 1 Barefoot Rehabilitation Instructor</li>
      <li>Foot Manual Therapies trained</li>
      <li>Fascial Lines trained</li>
      <li>Class 3b Laser Certified</li>
    </ul>
  </div>
  <div class="block stat stat--elite">
    <p style="margin-bottom:7px">Our Elite Athlete Experience :</p>
    <p>National Institute of Sport (NIS)</p>
    <p>National Rugby Squad</p>
    <p>Harbour City Games</p>
    <p>Coastline Triathlon Championships</p>
    <p>Southern Nations Games</p>
    <p>Westside Tennis Cup</p>
  </div>
  <h3 class="block partners__heading" style="font-weight:400">Referral Partners Required:</h3>
  <ul class="block partners__list">
    <li>Massage therapists<span class="sub">Deep tissue and remedial massage</span><span class="sub">Therapeutic massage</span></li>
    <li>Fascial therapists<span class="sub">Fascial lines releases to reset the alignment of the whole body</span></li>
    <li>Physiotherapists<span class="sub">Pain relief, protect and strengthen both lower limb and upper limb</span></li>
    <li>GP, Sports Physicians<span class="sub">General health, diagnostics, treatment support, prescription medications</span><span class="sub">Specialist referrals</span></li>
    <li>Osteopaths and chiropractors<span class="sub">Mobilisation and manipulative therapy for the spinal column and limbs</span></li>
    <li>Dietician and nutritionists<span class="sub">DEXA scan for bone density/lean mass/fat mass</span><span class="sub">Optimising gut health and nutrition - You are what you eat!</span></li>
    <li>Psychologists/psychiatrists<span class="sub">Sometimes our physical body cannot get better until we optimise a healthy mind</span></li>
    <li>Personal trainers, Pilates and yoga instructors<span class="sub">Create awesome body strength, flexibility and resilience</span></li>
    <li>Surgeons<span class="sub">When conservative methods are ineffective, surgical intervention works well</span></li>
  </ul>
  <div class="block badges" aria-label="Partner and accreditation badges">
    <span class="badge badge--ring"></span>
    <span class="badge badge--wide"></span>
    <span class="badge badge--tri"></span>
    <span class="badge badge--wide-red"></span>
    <span class="badge badge--square"></span>
  </div>
</section>

</body>
</html>
```